KORV PTY LTD - Business Cards

Design a modern business card - using the attached Designs.
Same design as on the front, apart from the names/numbers/emails to be different.
We want the cards to be very glossy to stand out, do I think the simple black/white/metallic will be effective.
Both lots of details below:

Tom Wrenshaw
Director
tom_korv@nulvane.com
0438 274 093

Lewis Corbyn
Director
lewis_korv@nulvane.com
0419 385 642

Industry/Entity Type

Business

```html
<!DOCTYPE html>
<html lang="en">
<head>
<meta charset="utf-8">
<title>KORV PTY LTD – Business Cards</title>
<link rel="stylesheet" href="https://fonts.googleapis.com/css2?family=Bitter:wght@400;500;700&display=swap">
<style>
  :root {
    --backdrop: #e4e2df;
    --card-white: #ffffff;
    --ink: #2b2b2b;
    --ink-soft: #4a4a4a;
    --rule: #cfcfcf;
    --band-dark: #3d3d3e;
    --band-mid: #a7a8a8;
    --band-faint: #5a5a5b;
    --metal-light: #f4f5f5;
    --metal-mid: #c9cbcc;
    --metal-dark: #9ea3a5;
  }
  * { box-sizing: border-box; margin: 0; padding: 0; }
  html, body { width: 1200px; height: 475px; overflow: hidden; }
  body {
    background: var(--backdrop);
    font-family: "Bitter", serif;
    color: var(--ink);
    position: relative;
  }
  .card {
    position: absolute;
    top: 62px;
    width: 560px;
    height: 350px;
    box-shadow: 0 4px 14px rgba(0,0,0,0.25);
    overflow: hidden;
  }
  .card--front { left: 25px; background: var(--card-white); }
  .card--back {
    left: 615px;
    background: linear-gradient(100deg, var(--metal-mid) 0%, var(--metal-light) 22%, var(--metal-light) 32%, var(--metal-mid) 55%, var(--metal-light) 72%, var(--metal-dark) 100%);
  }
  .brand {
    position: absolute;
    display: flex;
    align-items: center;
    gap: 10px;
    font-weight: 700;
    color: var(--band-dark);
    letter-spacing: 0.04em;
  }
  .brand__dot {
    width: 16px; height: 16px;
    border-radius: 50%;
    background: var(--band-dark);
  }
  .card--front .brand { left: 70px; top: 130px; font-size: 52px; }
  .card--back .brand { left: 50%; top: 50%; transform: translate(-50%, -50%); font-size: 96px; }
  .card--back .brand__dot { width: 26px; height: 26px; }
  .divider {
    position: absolute;
    left: 268px; top: 95px;
    width: 1px; height: 140px;
    background: var(--rule);
  }
  .details { position: absolute; left: 292px; top: 100px; }
  .details__name { font-size: 21px; font-weight: 500; }
  .details__role { font-size: 13px; margin-top: 6px; color: var(--ink-soft); }
  .details__contacts { list-style: none; margin-top: 32px; font-size: 14.5px; }
  .details__contacts li { display: flex; align-items: center; gap: 7px; margin-bottom: 4px; }
  .details__contacts svg { width: 12px; height: 12px; fill: var(--ink); }
  .bands { position: absolute; left: 0; bottom: 0; width: 560px; height: 130px; }
  .bands__mark {
    position: absolute;
    right: 40px; bottom: 62px;
    font-size: 34px; font-weight: 700;
    color: var(--band-faint);
    letter-spacing: 0.04em;
  }
</style>
</head>
<body>
  <section class="card card--front" aria-label="Business card front">
    <div class="brand"><span class="brand__dot"></span>KORV</div>
    <div class="divider"></div>
    <div class="details">
      <p class="details__name">Lewis Corbyn</p>
      <p class="details__role">Director</p>
      <ul class="details__contacts">
        <li><svg viewBox="0 0 24 24" aria-hidden="true"><path d="M6.6 10.8a15.1 15.1 0 0 0 6.6 6.6l2.2-2.2c.3-.3.7-.4 1-.2 1.1.4 2.3.6 3.6.6.6 0 1 .4 1 1V20c0 .6-.4 1-1 1A17 17 0 0 1 3 4c0-.6.4-1 1-1h3.5c.6 0 1 .4 1 1 0 1.3.2 2.5.6 3.6.1.3 0 .7-.2 1z"/></svg>0419 385 642</li>
        <li><svg viewBox="0 0 24 24" aria-hidden="true"><path d="M2 5h20v14H2z M2 5l10 8 10-8" fill="none" stroke="#2b2b2b" stroke-width="2.4"/></svg>lewis_korv@nulvane.com</li>
      </ul>
    </div>
    <svg class="bands" viewBox="0 0 560 130" aria-hidden="true">
      <polygon points="0,110 250,110 305,62 560,62 560,130 0,130" fill="var(--band-dark)"/>
      <polygon points="0,93 240,93 252,82 0,82" fill="var(--band-mid)"/>
      <polygon points="0,100 232,100 240,93 0,93" fill="var(--card-white)"/>
    </svg>
    <span class="bands__mark">KORV</span>
  </section>

  <section class="card card--back" aria-label="Business card back">
    <div class="brand"><span class="brand__dot"></span>KORV</div>
  </section>
</body>
</html>
```